Design concept for BrightKestrel.com Support Page

We are about to launch a new support page for our www.brightkestrel.com service for photographers and visual artists. The service provides media management, cloud storage, promotional and secure distribution to our members.

The support page will include FAQs and video tutorials.

In particular we're looking for a header for this page that suggests the user is in the support area of our service - so perhaps an illustration that suggests support could look nice (perhaps repair man or doctor iconography). Something to give this area of our site a different look and something that looks both cool and friendly.

Currently the page looks distinctly sparse and undesigned (see attached screenshot) - something that could be remedied, we feel, by some subtle design enhancements that we can implement using CSS.

```html
<!DOCTYPE html>
<html lang="en">
<head>
<meta charset="utf-8">
<title>BrightKestrel Support</title>
<link rel="stylesheet" href="https://fonts.googleapis.com/css2?family=Open+Sans:wght@300;400;600;700&family=Ubuntu:wght@400;500;700&display=swap">
<style>
  :root {
    --ink: #4a4f57;
    --logo: #5a6068;
    --sky-deep: #1693bd;
    --sky-mid: #5bb7d6;
    --sky-pale: #d9eef5;
    --accent: #29b3d5;
    --faq-row: #636870;
    --faq-line: #7b8088;
    --panel-grey: #eeeeee;
    --search-field: #bdbdbd;
    --footer-bg: #000000;
    --footer-link: #9a9a9a;
    --footer-muted: #6f6f6f;
    --white: #ffffff;
  }
  * { box-sizing: border-box; margin: 0; padding: 0; }
  html, body { width: 1031px; height: 1200px; overflow: hidden; background: var(--white); }
  body { position: relative; font-family: "Open Sans", Arial, sans-serif; color: var(--ink); }

  .site-header { position: absolute; left: 0; top: 0; width: 1031px; height: 80px; z-index: 2; }
  .brand { position: absolute; left: 26px; top: 16px; display: flex; align-items: center; gap: 10px; }
  .brand-mark { width: 36px; height: 36px; border: 4px solid var(--logo); border-radius: 4px; }
  .brand-name { font-family: "Ubuntu", sans-serif; font-weight: 500; font-size: 34px; color: var(--logo); letter-spacing: -0.5px; }
  .account-menu { position: absolute; left: 871px; top: 21px; width: 136px; height: 30px; border: 1px solid #cfcfcf; border-radius: 2px; background: var(--white); display: flex; align-items: center; padding-left: 6px; font-size: 12px; color: #333; }
  .account-avatar { width: 22px; height: 22px; background: linear-gradient(135deg, #6b5a4a, #c9b8a4); margin-right: 10px; }
  .account-caret { position: absolute; right: 10px; top: 11px; border-left: 4px solid transparent; border-right: 4px solid transparent; border-top: 6px solid #888; }

  .hero { position: absolute; left: 0; top: 0; width: 1031px; height: 433px; background: linear-gradient(180deg, var(--white) 0px, var(--white) 70px, var(--sky-pale) 120px, var(--sky-mid) 250px, var(--sky-deep) 433px); }
  .hero-badge { position: absolute; left: 448px; top: 151px; width: 136px; height: 136px; border-radius: 50%; border: 5px solid var(--white); display: flex; align-items: center; justify-content: center; }
  .hero-badge-inner { width: 112px; height: 112px; border-radius: 50%; background: var(--white); display: flex; align-items: center; justify-content: center; }
  .hero-kicker { position: absolute; left: 0; width: 1031px; top: 296px; text-align: center; font-size: 24px; color: var(--white); }
  .hero-title { position: absolute; left: 0; width: 1031px; top: 322px; text-align: center; font-size: 49px; font-weight: 300; color: var(--white); }

  .help-area { position: absolute; left: 0; top: 433px; width: 1031px; height: 613px; }
  .faq-panel { position: absolute; left: 0; top: 0; width: 515px; height: 613px; background: var(--white); }
  .video-panel { position: absolute; left: 515px; top: 0; width: 516px; height: 613px; background: var(--panel-grey); }
  .section-title { position: absolute; top: 52px; font-family: "Ubuntu", sans-serif; font-weight: 700; font-size: 31px; color: var(--ink); }
  .faq-panel .section-title { left: 34px; }
  .video-panel .section-title { left: 35px; }

  .faq-search { position: absolute; left: 129px; top: 57px; display: flex; height: 33px; }
  .faq-search-field { width: 267px; background: var(--search-field); }
  .faq-search-button { width: 91px; background: var(--accent); color: var(--white); font-size: 14px; display: flex; align-items: center; justify-content: center; }

  .faq-list { position: absolute; left: 33px; top: 107px; list-style: none; }
  .faq-item { width: 457px; height: 40px; margin-bottom: 2px; background: var(--faq-row); border-radius: 3px; display: flex; align-items: center; color: var(--white); font-size: 14.5px; border-bottom: 1px solid var(--faq-line); }
  .faq-item.is-open { background: var(--accent); font-size: 15px; }
  .faq-toggle { width: 22px; height: 22px; border-radius: 50%; background: var(--white); color: var(--accent); font-weight: 700; font-size: 17px; line-height: 22px; text-align: center; margin: 0 20px 0 23px; flex: none; }
  .faq-item.is-open .faq-toggle { margin-right: 21px; }

  .video-grid { position: absolute; left: 37px; top: 107px; display: grid; grid-template-columns: 219px 219px; gap: 11px 10px; }
  .video-tile { width: 219px; height: 219px; position: relative; display: flex; align-items: center; justify-content: center; }
  .video-tile.coffee { background: radial-gradient(circle at 50% 55%, #3a2a22 0 22%, #2f6f86 40%, #0d3a50 100%); }
  .video-tile.summit { background: linear-gradient(180deg, #7fc4c8 0%, #e9d58a 45%, #d69c4c 70%, #2a2a2a 100%); }
  .video-tile.strap { background: linear-gradient(135deg, #e9e2c8 0%, #c8a88a 40%, #2b2b2b 60%, #b58a5f 100%); }
  .video-tile.powder { background: radial-gradient(circle at 45% 60%, #e6d14a 0 15%, #4aa36a 35%, #2b5f9b 60%, #1a1a2e 100%); }
  .play-icon { width: 74px; height: 74px; }

  .site-footer { position: absolute; left: 0; top: 1046px; width: 1031px; height: 154px; background: var(--footer-bg); text-align: center; }
  .footer-nav { position: absolute; left: 0; width: 1031px; top: 34px; font-size: 13px; color: var(--footer-link); }
  .footer-nav span.sep { margin: 0 8px; }
  .footer-copy { position: absolute; left: 0; width: 1031px; top: 75px; font-size: 12.5px; font-weight: 600; color: var(--white); }
  .footer-powered { position: absolute; left: 0; width: 1031px; top: 97px; font-size: 12.5px; color: var(--footer-muted); }
</style>
</head>
<body>
  <section class="hero">
    <div class="hero-badge">
      <div class="hero-badge-inner">
        <svg width="54" height="54" viewBox="0 0 54 54" aria-hidden="true">
          <path d="M9 30 V24 a18 18 0 0 1 36 0 V30" fill="none" stroke="#4a4f57" stroke-width="4"/>
          <rect x="5" y="26" width="10" height="16" rx="4" fill="#4a4f57"/>
          <rect x="39" y="26" width="10" height="16" rx="4" fill="#4a4f57"/>
          <path d="M44 42 q0 8 -14 8" fill="none" stroke="#4a4f57" stroke-width="2.5"/>
          <circle cx="28" cy="50" r="3" fill="#4a4f57"/>
        </svg>
      </div>
    </div>
    <p class="hero-kicker">BrightKestrel Support</p>
    <h1 class="hero-title">We’re happy to help ...</h1>
  </section>

  <header class="site-header">
    <div class="brand">
      <span class="brand-mark"></span>
      <span class="brand-name">BrightKestrel</span>
    </div>
    <div class="account-menu">
      <span class="account-avatar" role="img" aria-label="Account avatar photo"></span>
      Maren Holt
      <span class="account-caret"></span>
    </div>
  </header>

  <main class="help-area">
    <section class="faq-panel">
      <h2 class="section-title">FAQ</h2>
      <div class="faq-search">
        <div class="faq-search-field"></div>
        <div class="faq-search-button">search</div>
      </div>
      <ul class="faq-list">
        <li class="faq-item is-open"><span class="faq-toggle">+</span>Uploading Files Using the Drag and Drop Uploader</li>
        <li class="faq-item"><span class="faq-toggle">+</span>Publishing Files</li>
        <li class="faq-item"><span class="faq-toggle">+</span>Creating Galleries</li>
        <li class="faq-item"><span class="faq-toggle">+</span>Creating Portfolios</li>
        <li class="faq-item"><span class="faq-toggle">+</span>Re-ordering Files within Galleries of Portfolios</li>
        <li class="faq-item"><span class="faq-toggle">+</span>Managing Folder and Files</li>
        <li class="faq-item"><span class="faq-toggle">+</span>Publishing Files</li>
        <li class="faq-item"><span class="faq-toggle">+</span>Creating Galleries</li>
        <li class="faq-item"><span class="faq-toggle">+</span>Creating Portfolios</li>
        <li class="faq-item"><span class="faq-toggle">+</span>Re-ordering Files within Galleries of Portfolios</li>
        <li class="faq-item"><span class="faq-toggle">+</span>Managing Folder and Files</li>
      </ul>
    </section>

    <section class="video-panel">
      <h2 class="section-title">Video Tutorials</h2>
      <div class="video-grid">
        <div class="video-tile coffee" role="img" aria-label="Tutorial thumbnail: close-up of a coffee bean on a blue background">
          <svg class="play-icon" viewBox="0 0 74 74" aria-hidden="true"><circle cx="37" cy="37" r="33" fill="none" stroke="rgba(255,255,255,0.75)" stroke-width="4"/><path d="M29 22 L54 37 L29 52 Z" fill="rgba(255,255,255,0.75)"/></svg>
        </div>
        <div class="video-tile summit" role="img" aria-label="Tutorial thumbnail: photographer silhouetted against a sunset sky">
          <svg class="play-icon" viewBox="0 0 74 74" aria-hidden="true"><circle cx="37" cy="37" r="33" fill="none" stroke="rgba(255,255,255,0.75)" stroke-width="4"/><path d="M29 22 L54 37 L29 52 Z" fill="rgba(255,255,255,0.75)"/></svg>
        </div>
        <div class="video-tile strap" role="img" aria-label="Tutorial thumbnail: film camera hanging from a strap">
          <svg class="play-icon" viewBox="0 0 74 74" aria-hidden="true"><circle cx="37" cy="37" r="33" fill="none" stroke="rgba(255,255,255,0.75)" stroke-width="4"/><path d="M29 22 L54 37 L29 52 Z" fill="rgba(255,255,255,0.75)"/></svg>
        </div>
        <div class="video-tile powder" role="img" aria-label="Tutorial thumbnail: hand throwing colourful powder">
          <svg class="play-icon" viewBox="0 0 74 74" aria-hidden="true"><circle cx="37" cy="37" r="33" fill="none" stroke="rgba(255,255,255,0.75)" stroke-width="4"/><path d="M29 22 L54 37 L29 52 Z" fill="rgba(255,255,255,0.75)"/></svg>
        </div>
      </div>
    </section>
  </main>

  <footer class="site-footer">
    <nav class="footer-nav">
      Home<span class="sep">·</span>Contact Us<span class="sep">·</span>Affiliate Program<span class="sep">·</span>Privacy Policy<span class="sep">·</span>Site Terms and Conditions<span class="sep">·</span>About Us
    </nav>
    <p class="footer-copy">© Copyright 2014 Northwind Imaging Pte Ltd. All rights reserved.</p>
    <p class="footer-powered">Powered by BrightKestrel</p>
  </footer>
</body>
</html>
```